Luxurious Product label and box for all natural skincare product. + 30AUD tip to winner.

What I require.
1.     One product label and one-box design.
2.     I must have a mock-up of the bottle with the attached label and the box.
 
I have supplied the following files for the designers to use.
1.     Brand logo file. (logo.zip)
2.     Slogan file. (slogan.psd)
3.     Slogan script file. (italianno.regular.ttf)
4.     Bottle image file. (60ml_moisturiser_bottle.png)
5.     Icon bar file. (Icon_bar_en.zip)
 
Label and box Design
I am interested in your unique design concepts and colors, so please feel free to be creative.
1.     Brand name: Velia
2.     You can use your own choice of colors in your design. I would prefer two colors (excluding logo and slogan colors), although more colors are acceptable for the right design.
3.     Label and box to have a background color or pattern.
4.     I would like the icon bar to wrap around the bottom of the label and box, covering the full width of all sides of the box.
5.     The height of the icon bar should be about 7mm to 10mm high.   
6.     The hex code for the icon bar color is #EDD6D4. The color of the icons can be any color the designer chooses.
7.     The positioning of the icons are as follows.
a)     The front panel has three icons. From left to right, they are; 100% Vegan, Product of Australia, and 100% Natural.
b)     The left side panel has three icons. From the front of the label/box to the back of the label/box, they are; Cruelty-Free, Ethical & Sustainable, and Please Recycle.
c)     The right side panel has only one icon situated at the front of the right side of the label/box. The icon is 6 Months Once Open.
 
Label.
1.     The label will be a three-panel label.
2.     The label will contain text in all three panels; however, only the text for the front panel of the label is supplied in this brief. For now, use Lorem Ipsum placeholder text to fill spaces.
3.     The final text will be provided to the winning designer so they can apply the text to the left and right panels of the label.
4.     Label size. Width 104mm x Height 83mm.
5.     The final design file must include bleed and cut lines.
 
Box.
1.     The box will contain text on all four sides; however, only the text for the front of the box is supplied in this brief. For now, use Lorem Ipsum placeholder text to fill spaces.
2.     The final text will be provided to the winning designer so they can apply the text to the left and right sides and the back of the box.
3.     The box size is 40mm wide x 40mm deep x 140mm high.
4.     The final design file must include bleed and cut lines.
 
Front Panel wording.
1.     Logo.
2.     Slogan.
3.     Moisturiser.
4.     Hydrate & Nourish.
5.     Hyaluronic Acid, Desert Lime & Green Tea.
6.     All Skin Types - Dry – Dehydrated.
7.     Icon bar.
8.     60mL
 
Bottle size
60ml White Bottle – 13.5cm High x 3.5cm Wide.

Target Market(s)

Beauty-minded Asian consumers between the age of 32 and 75 who take a proactive approach in maintaining younger-looking skin. Those who already know the danger of damaged skin caused by skincare containing harsh chemicals, and therefore choose effective natural/organic solutions to meet their skincare needs. Those who wish a more radiant glow and youthful appearance to their skin. Usually, a two-income middle to high-income bracket couple with a mindset for health and beauty.

Industry/Entity Type

Beauty and skincare.

Font styles to use
Other font styles liked:
• Logo and slogan script supplied. Designer to choose all other font or script.

Colors

Designer to choose colors to be used in the design.

Requirements
Must have
• A mock-up label on the bottle and a mock-up box. My logo and slogan are already designed with my chosen font and color.
Nice to have
• I like soft pastel colors with perhaps a small amount of stronger color.

```html
<!DOCTYPE html>
<html lang="en">
<head>
<meta charset="utf-8">
<title>Velia Moisturiser – Label and Box</title>
<link href="https://fonts.googleapis.com/css2?family=Barlow+Condensed:wght@300;400;500;600&family=Montserrat:wght@400&family=Libre+Franklin:wght@400;600;800&display=swap" rel="stylesheet">
<style>
:root{
  --ink:#4d4d4f;
  --bar:#4f4f51;
  --pink:#f1d6d3;
  --blush:#ecd8cc;
  --mist:#d9e2e3;
  --sage:#c8d8cb;
  --clay:#d9b9ad;
  --stage:#6d6e71;
  --line:#222;
  --white:#fff;
}
*{box-sizing:border-box;margin:0;padding:0}
html,body{width:755px;height:1200px;overflow:hidden;background:var(--white)}
.canvas{position:relative;width:755px;height:1200px;overflow:hidden}
.stage-band{position:absolute;inset:0}
.abs{position:absolute}

/* label */
.label{position:absolute;left:102px;top:60px;width:550px;height:438px;overflow:hidden;
  background:var(--pink);box-shadow:0 2px 6px rgba(0,0,0,.25)}
.wash{position:absolute;border-radius:50%;filter:blur(2px)}
.copy{font-family:'Montserrat',sans-serif;color:var(--ink);text-align:center}
.tagline{font-family:'Barlow Condensed',sans-serif;font-weight:400;color:var(--white);text-align:center;line-height:1;letter-spacing:.5px}
.banner{position:absolute;background:var(--bar);clip-path:polygon(0 0,100% 0,100% 100%,0 88%)}
.brand{font-family:'Barlow Condensed',sans-serif;font-weight:400;color:var(--ink);line-height:1;position:absolute}
.product{font-family:'Barlow Condensed',sans-serif;color:var(--ink);position:absolute;line-height:1.05}
.product b{font-weight:600;display:block}
.product span{font-weight:400;display:block}
.actives{position:absolute;background:var(--bar);color:var(--white);font-family:'Barlow Condensed',sans-serif;
  font-weight:300;line-height:1.15;border-radius:0 40px 0 0}
.skin{position:absolute;font-family:'Barlow Condensed',sans-serif;font-weight:400;color:var(--ink);line-height:1.2}
.icon-bar{position:absolute;background:var(--bar)}
.icon{position:absolute;text-align:center;color:var(--pink);font-family:'Montserrat',sans-serif;line-height:1.1;transform:translateX(-50%)}
.icon svg{display:block;margin:0 auto}
.barcode{position:absolute;background:var(--bar);color:var(--white);font-family:'Montserrat',sans-serif;
  display:flex;align-items:center;justify-content:center}
.volume{position:absolute;font-family:'Montserrat',sans-serif;color:var(--ink);transform:translateX(-50%)}

/* nutrition panel */
.nf{position:absolute;background:var(--white);border:1px solid #555;padding:.35em .5em .3em;
  font-family:'Libre Franklin',sans-serif;color:#333;line-height:1.28}
.nf-title{font-weight:800;font-size:2.75em;line-height:1;border-bottom:.08em solid #888;padding-bottom:.05em}
.nf-serv{font-size:1.15em}
.nf-size{display:flex;justify-content:space-between;font-weight:800;font-size:1.3em;border-bottom:.6em solid #333;padding-bottom:.1em}
.nf-small{font-size:.85em;font-weight:800;padding-top:.2em}
.nf-cal{display:flex;justify-content:space-between;font-weight:800;font-size:2.2em;line-height:1;border-bottom:.18em solid #333}
.nf-dv{text-align:right;font-size:.8em;font-weight:800;padding:.1em 0}
.nf-row{display:flex;justify-content:space-between;border-top:.1em solid #999}
.nf-row b{font-weight:800}
.nf-row .pct{font-weight:800}
.in1{padding-left:1.4em}
.in2{padding-left:2.8em}

/* dieline */
.dieline{position:absolute;left:0;top:0}
.panel{position:absolute;top:667px;width:116px;height:403px;overflow:hidden;background:var(--pink)}
</style>
</head>
<body>
<div class="canvas">

  <svg class="stage-band" width="755" height="1200" aria-hidden="true">
    <polygon points="20,0 755,0 755,582 652,498 102,60" fill="var(--stage)"/>
  </svg>

  <!-- LABEL -->
  <section class="label" aria-label="Bottle label">
    <div class="wash" style="left:-60px;top:-40px;width:170px;height:150px;background:radial-gradient(circle,var(--sage),rgba(200,216,203,0) 70%)"></div>
    <div class="wash" style="left:330px;top:-40px;width:260px;height:300px;background:radial-gradient(circle,var(--mist) 40%,rgba(217,226,227,0) 72%)"></div>
    <div class="wash" style="left:80px;top:270px;width:330px;height:240px;background:radial-gradient(circle,#e6d6c8 40%,rgba(230,214,200,0) 72%)"></div>
    <div class="wash" style="left:400px;top:250px;width:200px;height:200px;background:radial-gradient(circle,#d7c3b6 30%,rgba(215,195,182,0) 70%)"></div>

    <div class="copy abs" style="left:30px;top:68px;width:124px;font-size:8.3px;line-height:1.22">
      <p>Lorem ipsum dolor sit amet, consectetuer adipiscing elit, sed diam nonummy nibh euismod tincidunt ut laoreet dolore magna aliquam erat volutpat.</p>
      <p style="margin-top:11px">Lorem ipsum dolor sit amet, consectetuer adipiscing elit, sed diam nonummy nibh euismod tincidunt ut laoreet dolore magna aliquam erat volutpat.</p>
      <p style="margin-top:11px">Lorem ipsum dolor sit amet, consectetuer adipiscing elit, sed diam nonummy nibh euismod tincidunt ut laoreet dolore magna aliquam erat volutpat.</p>
      <p style="margin-top:11px">Lorem ipsum dolor sit amet, consectetuer adipiscing elit, sed diam nonummy nibh euismod tincidunt ut laoreet dolore magna aliquam erat volutpat.</p>
    </div>

    <div class="banner" style="left:197px;top:0;width:158px;height:73px">
      <p class="tagline" style="margin-top:28px;font-size:16px">rooted in botanics</p>
    </div>
    <p class="brand" style="left:200px;top:104px;font-size:56px;letter-spacing:1px">Velia</p>

    <div class="product" style="left:200px;top:203px">
      <b style="font-size:29px;letter-spacing:.5px">MOISTURISER</b>
      <span style="font-size:18px;margin-top:2px">Hydrate &amp; Nourish</span>
    </div>
    <div class="actives" style="left:197px;top:259px;width:158px;height:42px;padding:5px 0 0 9px;font-size:14.5px">
      Hyaluronic Acid<br>Desert Lime &amp; Green Tea.
    </div>
    <p class="skin" style="left:199px;top:303px;font-size:13.5px">All Skin Types Dry – Dehydrated</p>

    <div class="nf" style="left:381px;top:48px;width:156px;font-size:7px">
      <div class="nf-title">Nutrition Facts</div>
      <div class="nf-serv">10 servings per container</div>
      <div class="nf-size"><span>Serving size</span><span>1 cup (55g)</span></div>
      <div class="nf-small">Amount per serving</div>
      <div class="nf-cal"><span>Calories</span><span>165</span></div>
      <div class="nf-dv">% Daily Value*</div>
      <div class="nf-row"><span><b>Total Fat</b> 1.5g</span><span class="pct">2%</span></div>
      <div class="nf-row in1"><span>Saturated Fat 0.5g</span><span class="pct">3%</span></div>
      <div class="nf-row in1"><span><i>Trans</i> Fat 0g</span></div>
      <div class="nf-row in1"><span>Polyunsaturated Fat 0.5g</span></div>
      <div class="nf-row in1"><span>Monounsaturated Fat 0.5g</span></div>
      <div class="nf-row"><span><b>Cholesterol</b> 0mg</span><span class="pct">0%</span></div>
      <div class="nf-row"><span><b>Sodium</b> 180mg</span><span class="pct">8%</span></div>
      <div class="nf-row"><span><b>Fluoride</b> 0g</span></div>
      <div class="nf-row"><span><b>Total Carbohydrate</b> 21g</span><span class="pct">8%</span></div>
      <div class="nf-row in1"><span>Dietary Fiber 2g</span><span class="pct">7%</span></div>
      <div class="nf-row in2"><span>Soluble Fiber &lt;1g</span></div>
      <div class="nf-row in2"><span>Insoluble Fiber 1g</span></div>
      <div class="nf-row in1"><span>Total Sugars 8g</span></div>
    </div>
    <p class="copy abs" style="left:388px;top:300px;width:146px;font-size:8.3px;line-height:1.22">Lorem ipsum dolor sit amet, consectetuer adipiscing elit, sed diam nonummy nibh euismod tincidunt ut laoreet volutpat.</p>

    <div class="icon-bar" style="left:0;top:344px;width:550px;height:53px"></div>
    <div class="icon" style="left:49px;top:352px;font-size:5.5px">
      <svg width="26" height="24" viewBox="0 0 26 24" fill="none" stroke="var(--pink)" stroke-width="1.4"><path d="M9 8 L13 2 L17 8 M20 12 L24 19 L16 19 M6 19 L2 19 L6 12"/><path d="M11 4 L8 2 M18 20 L20 22 M4 16 L2 19"/></svg>
      Please<br>Recycle</div>
    <div class="icon" style="left:93px;top:352px;font-size:5.5px">
      <svg width="24" height="24" viewBox="0 0 24 24" fill="none" stroke="var(--pink)" stroke-width="1.2"><circle cx="12" cy="12" r="10"/><ellipse cx="12" cy="12" rx="4.5" ry="10"/><path d="M2 12 H22"/></svg>
      Ethical &amp;<br>Sustainable</div>
    <div class="icon" style="left:134px;top:352px;font-size:5.5px">
      <svg width="24" height="24" viewBox="0 0 24 24" role="img" aria-label="Cruelty free badge"><circle cx="12" cy="13" r="9" fill="var(--pink)" opacity=".85"/></svg>
      Cruelty<br>Free</div>
    <div class="icon" style="left:211px;top:352px;font-size:5.5px;font-weight:600">
      <svg width="24" height="24" viewBox="0 0 24 24" fill="none" stroke="var(--pink)" stroke-width="1.6"><path d="M12 21 C4 14 2 10 3.5 6.5 C5 3 10 3 12 7 C14 3 19 3 20.5 6.5 C22 10 20 14 12 21Z"/></svg>
      100%<br>Vegan</div>
    <div class="icon" style="left:275px;top:352px;font-size:5.5px">
      <svg width="40" height="24" viewBox="0 0 40 24" role="img" aria-label="Australian origin badge"><rect x="6" y="5" width="28" height="16" rx="8" fill="var(--pink)" opacity=".85"/></svg>
      Product of<br>Australia</div>
    <div class="icon" style="left:335px;top:352px;font-size:5.5px">
      <svg width="26" height="24" viewBox="0 0 26 24" fill="none" stroke="var(--pink)" stroke-width="1.4"><path d="M13 20 C8 15 9 7 13 3 C17 7 18 15 13 20Z"/><path d="M12 21 C5 21 2 16 2 10 C7 11 11 15 12 21Z"/><path d="M14 21 C21 21 24 16 24 10 C19 11 15 15 14 21Z"/></svg>
      100%<br>Natural</div>
    <div class="barcode" style="left:387px;top:353px;width:103px;height:56px;font-size:8px">bar code</div>
    <div class="icon" style="left:518px;top:352px;font-size:5.5px">
      <svg width="18" height="20" viewBox="0 0 18 20" fill="none" stroke="var(--pink)" stroke-width="1.1"><rect x="3" y="2" width="12" height="3"/><rect x="2" y="6" width="14" height="11"/><text x="9" y="14.5" font-size="6" text-anchor="middle" fill="var(--pink)" stroke="none" font-family="Montserrat,sans-serif">6M</text></svg>
      6 Months<br>Once Open</div>
    <p class="volume" style="left:276px;top:407px;font-size:12px">60mL</p>
  </section>

  <!-- BOX DIELINE -->
  <svg class="dieline" width="755" height="1200" fill="none" stroke="var(--line)" stroke-width=".8" aria-label="Box dieline">
    <path d="M171 667 V615 L165 605 V600 H265 V605 L259 615 V667"/>
    <path d="M411 667 V615 L405 605 V600 H501 V605 L495 615 V667"/>
    <path d="M510 667 V570 H627 V667 M510 570 V555 Q510 537 528 537 H609 Q627 537 627 555 V570"/>
    <path d="M165 680 L128 693 V1057 L165 1068"/>
    <path d="M171 1070 V1092 L165 1100 V1137 H265 V1100 L259 1092 V1070"/>
    <path d="M411 1070 V1092 L405 1100 V1137 H501 V1100 L495 1092 V1070"/>
    <path d="M280 1070 V1172 H396 V1070 M280 1172 V1185 Q280 1200 295 1200 M396 1172 V1185 Q396 1200 381 1200"/>
  </svg>

  <!-- left side panel -->
  <div class="panel" style="left:165px" aria-label="Box left side">
    <div class="wash" style="left:-20px;top:-20px;width:110px;height:90px;background:radial-gradient(circle,var(--sage),rgba(200,216,203,0) 70%)"></div>
    <div class="wash" style="left:-30px;top:250px;width:180px;height:200px;background:radial-gradient(circle,var(--blush) 40%,rgba(236,216,204,0) 72%)"></div>
    <div class="copy abs" style="left:10px;top:22px;width:96px;font-size:6px;line-height:1.2">
      <p>Lorem ipsum dolor sit amet, consectetuer adipiscing elit, sed diam nonummy nibh euismod tincidunt ut laoreet dolore magna aliquam erat volutpat.</p>
      <p style="margin-top:7px">Lorem ipsum dolor sit amet, consectetuer adipiscing elit, sed diam nonummy nibh euismod tincidunt ut laoreet dolore magna aliquam erat volutpat.</p>
      <p style="margin-top:7px">Lorem ipsum dolor sit amet, consectetuer adipiscing elit, sed diam nonummy nibh euismod tincidunt ut laoreet dolore magna aliquam erat volutpat.</p>
      <p style="margin-top:7px">Lorem ipsum dolor sit amet, consectetuer adipiscing elit, sed diam nonummy nibh euismod tincidunt ut laoreet dolore magna aliquam erat volutpat.</p>
      <p style="margin-top:7px">Lorem ipsum dolor sit amet, consectetuer adipiscing elit, sed diam nonummy nibh euismod tincidunt ut laoreet dolore magna aliquam erat volutpat.</p>
      <p style="margin-top:7px">Lorem ipsum dolor sit amet, consectetuer adipiscing elit, sed diam nonummy nibh euismod tincidunt ut laoreet dolore magna aliquam erat volutpat.</p>
    </div>
    <div class="icon-bar" style="left:0;top:340px;width:116px;height:30px"></div>
    <div class="icon" style="left:32px;top:343px;font-size:3px"><svg width="14" height="13" viewBox="0 0 26 24" fill="none" stroke="var(--pink)" stroke-width="1.6"><path d="M9 8 L13 2 L17 8 M20 12 L24 19 L16 19 M6 19 L2 19 L6 12"/></svg>Please<br>Recycle</div>
    <div class="icon" style="left:56px;top:343px;font-size:3px"><svg width="14" height="13" viewBox="0 0 24 24" fill="none" stroke="var(--pink)" stroke-width="1.4"><circle cx="12" cy="12" r="10"/><ellipse cx="12" cy="12" rx="4.5" ry="10"/></svg>Ethical &amp;<br>Sustainable</div>
    <div class="icon" style="left:80px;top:343px;font-size:3px"><svg width="14" height="13" viewBox="0 0 24 24" role="img" aria-label="Cruelty free badge"><circle cx="12" cy="13" r="9" fill="var(--pink)" opacity=".85"/></svg>Cruelty<br>Free</div>
  </div>

  <!-- front panel -->
  <div class="panel" style="left:280px" aria-label="Box front">
    <div class="wash" style="left:50px;top:10px;width:120px;height:140px;background:radial-gradient(circle,var(--mist) 30%,rgba(217,226,227,0) 70%)"></div>
    <div class="wash" style="left:-40px;top:280px;width:200px;height:160px;background:radial-gradient(circle,var(--blush) 40%,rgba(236,216,204,0) 72%)"></div>
    <div class="banner" style="left:8px;top:0;width:99px;height:57px"><p class="tagline" style="margin-top:29px;font-size:11px">rooted in botanics</p></div>
    <p class="brand" style="left:10px;top:88px;font-size:40px">Velia</p>
    <div class="product" style="left:15px;top:175px">
      <b style="font-size:17px">MOISTURISER</b>
      <span style="font-size:16px;font-weight:300;margin-top:3px;line-height:1.2">Hydrate<br>&amp; Nourish</span>
    </div>
    <div class="actives" style="left:15px;top:240px;width:87px;height:43px;padding:3px 0 0 4px;font-size:11.5px;line-height:1;border-radius:0 26px 0 0">Hyaluronic Acid<br>Desert Lime &amp;<br>Green Tea.</div>
    <p class="skin" style="left:15px;top:286px;font-size:10px;font-weight:300">All Skin Types<br>Dry – Dehydrated</p>
    <div class="icon-bar" style="left:0;top:340px;width:116px;height:30px"></div>
    <div class="icon" style="left:23px;top:343px;font-size:3px"><svg width="14" height="13" viewBox="0 0 24 24" fill="none" stroke="var(--pink)" stroke-width="2"><path d="M12 21 C4 14 2 10 3.5 6.5 C5 3 10 3 12 7 C14 3 19 3 20.5 6.5 C22 10 20 14 12 21Z"/></svg>100%<br>Vegan</div>
    <div class="icon" style="left:57px;top:343px;font-size:3px"><svg width="22" height="13" viewBox="0 0 40 24" role="img" aria-label="Australian origin badge"><rect x="6" y="5" width="28" height="16" rx="8" fill="var(--pink)" opacity=".85"/></svg>Product of<br>Australia</div>
    <div class="icon" style="left:93px;top:343px;font-size:3px"><svg width="14" height="13" viewBox="0 0 26 24" fill="none" stroke="var(--pink)" stroke-width="1.8"><path d="M13 20 C8 15 9 7 13 3 C17 7 18 15 13 20Z"/><path d="M12 21 C5 21 2 16 2 10 C7 11 11 15 12 21Z"/><path d="M14 21 C21 21 24 16 24 10 C19 11 15 15 14 21Z"/></svg>100%<br>Natural</div>
    <p class="volume" style="left:58px;top:374px;font-size:8px">60mL</p>
  </div>

  <!-- right side panel -->
  <div class="panel" style="left:396px" aria-label="Box right side">
    <div class="wash" style="left:-40px;top:-30px;width:150px;height:150px;background:radial-gradient(circle,var(--mist) 30%,rgba(217,226,227,0) 70%)"></div>
    <div class="wash" style="left:-30px;top:260px;width:180px;height:180px;background:radial-gradient(circle,var(--blush) 40%,rgba(236,216,204,0) 72%)"></div>
    <div class="nf" style="left:8px;top:20px;width:99px;font-size:4.4px">
      <div class="nf-title">Nutrition Facts</div>
      <div class="nf-serv">10 servings per container</div>
      <div class="nf-size"><span>Serving size</span><span>1 cup (55g)</span></div>
      <div class="nf-small">Amount per serving</div>
      <div class="nf-cal"><span>Calories</span><span>165</span></div>
      <div class="nf-dv">% Daily Value*</div>
      <div class="nf-row"><span><b>Total Fat</b> 1.5g</span><span class="pct">2%</span></div>
      <div class="nf-row in1"><span>Saturated Fat 0.5g</span><span class="pct">3%</span></div>
      <div class="nf-row in1"><span><i>Trans</i> Fat 0g</span></div>
      <div class="nf-row in1"><span>Polyunsaturated Fat 0.5g</span></div>
      <div class="nf-row in1"><span>Monounsaturated Fat 0.5g</span></div>
      <div class="nf-row"><span><b>Cholesterol</b> 0mg</span><span class="pct">0%</span></div>
      <div class="nf-row"><span><b>Sodium</b> 180mg</span><span class="pct">8%</span></div>
      <div class="nf-row"><span><b>Fluoride</b> 0g</span></div>
      <div class="nf-row"><span><b>Total Carbohydrate</b> 21g</span><span class="pct">8%</span></div>
      <div class="nf-row in1"><span>Dietary Fiber 2g</span><span class="pct">7%</span></div>
      <div class="nf-row in2"><span>Soluble Fiber &lt;1g</span></div>
      <div class="nf-row in2"><span>Insoluble Fiber 1g</span></div>
      <div class="nf-row in1"><span>Total Sugars 8g</span></div>
    </div>
    <div class="copy abs" style="left:10px;top:188px;width:96px;font-size:5.4px;line-height:1.2">
      <p>Lorem ipsum dolor sit amet, consectetuer adipiscing elit, sed diam nonummy nibh euismod tincidunt ut laoreet dolore magna aliquam erat volutpat.</p>
      <p style="margin-top:7px">Lorem ipsum dolor sit amet, consectetuer adipiscing elit, sed diam nonummy nibh euismod tincidunt ut laoreet dolore magna aliquam erat volutpat.</p>
      <p style="margin-top:7px">Lorem ipsum dolor sit amet, consectetuer adipiscing elit, sed diam nonummy nibh euismod tincidunt ut laoreet dolore magna aliquam erat volutpat.</p>
      <p style="margin-top:7px">Lorem ipsum dolor sit amet, consectetuer adipiscing elit, sed diam nonummy nibh euismod tincidunt ut laoreet dolore magna aliquam erat volutpat.</p>
    </div>
    <div class="icon-bar" style="left:0;top:340px;width:116px;height:30px"></div>
    <div class="barcode" style="left:9px;top:344px;width:68px;height:37px;font-size:7.5px;background:var(--clay);color:var(--ink)">bar code</div>
    <div class="icon" style="left:94px;top:343px;font-size:3px"><svg width="12" height="13" viewBox="0 0 18 20" fill="none" stroke="var(--pink)" stroke-width="1.3"><rect x="3" y="2" width="12" height="3"/><rect x="2" y="6" width="14" height="11"/><text x="9" y="14.5" font-size="6" text-anchor="middle" fill="var(--pink)" stroke="none" font-family="Montserrat,sans-serif">6M</text></svg>6 Months<br>Once Open</div>
  </div>

  <!-- back panel (front repeat) -->
  <div class="panel" style="left:511px;background:var(--mist)" aria-label="Box back">
    <div class="wash" style="left:-50px;top:-30px;width:120px;height:160px;background:radial-gradient(circle,var(--pink) 30%,rgba(241,214,211,0) 70%)"></div>
    <div class="wash" style="left:20px;top:200px;width:160px;height:180px;background:radial-gradient(circle,#d9c2b6 30%,rgba(217,194,182,0) 70%)"></div>
    <div class="wash" style="left:-40px;top:300px;width:200px;height:160px;background:radial-gradient(circle,var(--blush) 40%,rgba(236,216,204,0) 72%)"></div>
    <div class="banner" style="left:8px;top:0;width:99px;height:57px"><p class="tagline" style="margin-top:29px;font-size:11px">rooted in botanics</p></div>
    <p class="brand" style="left:10px;top:88px;font-size:40px">Velia</p>
    <div class="product" style="left:15px;top:175px">
      <b style="font-size:17px">MOISTURISER</b>
      <span style="font-size:16px;font-weight:300;margin-top:3px;line-height:1.2">Hydrate<br>&amp; Nourish</span>
    </div>
    <div class="actives" style="left:15px;top:240px;width:87px;height:43px;padding:3px 0 0 4px;font-size:11.5px;line-height:1;border-radius:0 26px 0 0">Hyaluronic Acid<br>Desert Lime &amp;<br>Green Tea.</div>
    <p class="skin" style="left:15px;top:286px;font-size:10px;font-weight:300">All Skin Types<br>Dry – Dehydrated</p>
    <div class="icon-bar" style="left:0;top:340px;width:116px;height:30px"></div>
    <div class="icon" style="left:23px;top:343px;font-size:3px"><svg width="14" height="13" viewBox="0 0 24 24" fill="none" stroke="var(--pink)" stroke-width="2"><path d="M12 21 C4 14 2 10 3.5 6.5 C5 3 10 3 12 7 C14 3 19 3 20.5 6.5 C22 10 20 14 12 21Z"/></svg>100%<br>Vegan</div>
    <div class="icon" style="left:57px;top:343px;font-size:3px"><svg width="22" height="13" viewBox="0 0 40 24" role="img" aria-label="Australian origin badge"><rect x="6" y="5" width="28" height="16" rx="8" fill="var(--pink)" opacity=".85"/></svg>Product of<br>Australia</div>
    <div class="icon" style="left:93px;top:343px;font-size:3px"><svg width="14" height="13" viewBox="0 0 26 24" fill="none" stroke="var(--pink)" stroke-width="1.8"><path d="M13 20 C8 15 9 7 13 3 C17 7 18 15 13 20Z"/><path d="M12 21 C5 21 2 16 2 10 C7 11 11 15 12 21Z"/><path d="M14 21 C21 21 24 16 24 10 C19 11 15 15 14 21Z"/></svg>100%<br>Natural</div>
    <p class="volume" style="left:58px;top:374px;font-size:8px">60mL</p>
  </div>

  <svg class="dieline" width="755" height="1200" fill="none" stroke="var(--line)" stroke-width=".8" aria-hidden="true">
    <rect x="165" y="667" width="462" height="403"/>
    <path d="M280 667 V1070 M396 667 V1070 M511 667 V1070"/>
  </svg>
</div>
</body>
</html>
```